Anzeigengestaltung für einen einen ambulanten Pflegedienst
Zielgruppe
Insgesamt möchte ich gern drei Anzeigen für das Internet gestalten haben. Ich betreibe einen ambulanten Pflegedienst. Die erste Anzeige soll dazu dienen Kunden anzusprechen, die einen Unterstützungsbedarf und / oder einen Beratungsbedarf haben. Die zweite Anzeige soll dazu dienen neues Personal anzuwerben. Die dritte Anzeige soll speziell potenzielle Azubis ansprechen. Die Anzeigen sind gedacht für Tralvio und Pexumora hauptsächlich. In den Druck sollte es schon 10cm x 8cm sein. Es wäre super wenn vielleicht auch eine Art Aufruf an ehrenamtliche Mitarbeiter erfolgt.
Aufgabenstellung
Die Anzeigen sollen den Stil der Homepage beibehalten. Freundlich, frisch und agil wirken. Alle sollten emotional ansprechend sein und gerade der für zukünftige Mitarbeiter sollte deutlich ein gutes Betriebsklima vermitteln. Als Datei habe ich einige Bilder, die bereits für die Homepage oder Flyer verwendet wurden hochgeladen. des Weiteren habe ich die einzelnen Seiten des Flyers hochgeladen.

```html
<!DOCTYPE html>
<html lang="de">
<head>
<meta charset="utf-8">
<title>Stellenanzeige – Velumbra Pflege</title>
<link rel="stylesheet" href="https://fonts.googleapis.com/css2?family=Quicksand:wght@500;600;700&family=Playfair+Display:wght@400&display=swap">
<style>
  :root {
    --teal: #47aea9;
    --green: #7aac3a;
    --grey: #5f5f5f;
    --grey-soft: #6a6a6a;
    --sky: #e1f1f8;
    --white: #ffffff;
    --ring: #ecece6;
  }
  * { margin: 0; padding: 0; box-sizing: border-box; }
  html, body { width: 1200px; height: 960px; overflow: hidden; background: var(--white); }
  .ad {
    position: relative; width: 1200px; height: 960px; overflow: hidden;
    background: var(--white); font-family: "Quicksand", sans-serif; color: var(--grey);
  }
  .footer-band { position: absolute; left: 0; top: 840px; width: 1200px; height: 120px; background: var(--sky); }
  .hero-photo { position: absolute; left: 0; top: 0; width: 1200px; height: 960px; }
  .tagline {
    position: absolute; left: 60px; top: 58px;
    font-family: "Playfair Display", serif; font-size: 35px; color: var(--grey-soft); letter-spacing: 0.2px;
  }
  .headline {
    position: absolute; left: 58px; top: 106px;
    font-weight: 700; font-size: 63px; line-height: 76px; letter-spacing: 0.5px;
  }
  .headline .line-teal { color: var(--teal); display: block; }
  .headline .line-green { color: var(--green); display: block; }
  .divider { position: absolute; left: 60px; top: 297px; width: 303px; height: 6px; background: var(--green); }
  .mission {
    position: absolute; left: 60px; top: 329px; width: 500px;
    font-weight: 500; font-size: 32.5px; line-height: 42.5px; color: var(--grey); letter-spacing: 0.4px;
  }
  .promise {
    position: absolute; left: -6px; top: 547px; width: 326px; height: 326px;
    border-radius: 50%; background: var(--green);
  }
  .promise-text {
    position: absolute; left: 10px; top: 626px; width: 300px;
    transform: rotate(-9deg); transform-origin: center;
    color: var(--white); text-align: center; font-weight: 600; font-size: 28px; line-height: 36px;
  }
  .promise-text .promise-title { font-weight: 700; font-size: 29px; display: block; }
  .requirements {
    position: absolute; top: 557px; list-style: none;
    font-weight: 500; font-size: 33px; line-height: 59px; color: var(--grey); letter-spacing: 0.4px;
  }
  .requirements li { position: relative; padding-left: 28px; }
  .requirements li::before { content: "+"; position: absolute; left: 0; top: 0; color: var(--green); font-weight: 600; }
  .requirements.col-a { left: 360px; }
  .requirements.col-b { left: 703px; }
  .requirements .wrap { line-height: 46px; margin-top: 6px; }
  .url-pill {
    position: absolute; left: 300px; top: 869px; width: 586px; height: 62px;
    border-radius: 31px; background: var(--teal); color: var(--white);
    font-family: "Playfair Display", serif; font-size: 33px;
    display: flex; align-items: center; justify-content: center;
  }
  .brand-badge {
    position: absolute; left: 941px; top: 716px; width: 216px; height: 216px;
    border-radius: 50%; background: var(--white); border: 4px solid var(--ring);
    display: flex; flex-direction: column; align-items: center; justify-content: center; gap: 12px;
  }
  .brand-dot { width: 34px; height: 34px; border-radius: 50%; background: var(--teal); }
  .brand-name {
    font-weight: 700; font-size: 21px; line-height: 25px; color: var(--grey); text-align: center; letter-spacing: 0.3px;
  }
</style>
</head>
<body>
<main class="ad">
  <div class="footer-band"></div>

  <svg class="hero-photo" viewBox="0 0 1200 960">
    <defs>
      <radialGradient id="photo-tones" cx="0.45" cy="0.55" r="0.7">
        <stop offset="0" stop-color="#e8cdb2"/>
        <stop offset="0.45" stop-color="#c79f7c"/>
        <stop offset="0.8" stop-color="#8f8a84"/>
        <stop offset="1" stop-color="#5d6672"/>
      </radialGradient>
    </defs>
    <circle cx="1042" cy="56" r="490" fill="url(#photo-tones)" role="img"
            aria-label="Foto: Pflegeteam legt im Kreis die Hände übereinander, von unten fotografiert vor herbstlichen Bäumen"/>
    <path d="M548,318 C546,262 580,230 630,229 C662,228 690,234 703,243"
          fill="none" stroke="var(--teal)" stroke-width="7" stroke-linecap="round"/>
    <path d="M575,377 C578,322 590,285 607,277 C636,263 690,266 722,283"
          fill="none" stroke="var(--green)" stroke-width="7" stroke-linecap="round"/>
  </svg>

  <p class="tagline">Pflege mit Herz &amp; Seele</p>
  <h1 class="headline">
    <span class="line-teal">Komm in unser</span>
    <span class="line-green">Velumbra-Team!</span>
  </h1>
  <div class="divider"></div>
  <p class="mission">Hilf uns die Pflege in der Umgebung Dessau-Roßlau qualitativ zu verbessern und menschlicher zu gestalten.</p>

  <div class="promise"></div>
  <p class="promise-text">
    <span class="promise-title">Wir garantieren:</span>
    - Urlaub<br>
    - Fortbildungen<br>
    - TOP Vergütung<br>
    …
  </p>

  <ul class="requirements col-a">
    <li>Teamfähigkeit</li>
    <li>Hilfsbereitschaft</li>
    <li>Engagement</li>
  </ul>
  <ul class="requirements col-b">
    <li>Führerschein Klasse B</li>
    <li class="wrap">Gute Deutschkenntnisse<br>in Wort/Schrift</li>
  </ul>

  <div class="url-pill">www.velumbra-pflege.de/karriere/</div>

  <div class="brand-badge">
    <span class="brand-dot"></span>
    <span class="brand-name">VELUMBRA<br>PFLEGE</span>
  </div>
</main>
</body>
</html>
```